New business card for a regional office of a US M&A company

We need business card for a finance company, office based in Hong Kong , our Head office is in US, our business is to Merge and acquires companies , the new office will be a regional office for the Asia Pacific region. We want to use the head office logo as attached ( but don't have to be exactly the same, can be a variation to it) as a base and then add Asia Pacific alongside the logo.
We would prefer to have be bilingual Eng + Chinese, although we don't really have Chinese company name .

Industry/Entity Type

Business

Contact Information for Business Card

Clara Jo Tsang
 

VP,
APAC M&A Operations
Orin Vantage Asia Pacific Limited
 
Unit 1407, K18
18 Tai Lok Shan Road, 
Hong Kong 
 
M: +852 6038 1742
T : +852 2836 4100
F : +852 2836 4177
VOIP: 4158
 
cjtsang@orinvantage.com

Font styles to use
Serif
Sans Serif

Colors

Designer to choose colors to be used in the design.

Requirements
Must have
• APAC Office

```html
<!DOCTYPE html>
<html lang="en">
<head>
<meta charset="utf-8">
<title>Orin Vantage — Business Card</title>
<link href="https://fonts.googleapis.com/css2?family=Open+Sans:wght@400;600;700;800&display=swap" rel="stylesheet">
<style>
  :root {
    --backdrop: #2b2b2d;
    --card: #1c1c1e;
    --card-back: #202023;
    --front-mark: #3c3c3f;
    --accent: #21a9d6;
    --ink: #ffffff;
    --muted: #9a9aa0;
    --faint: #2a2a2d;
  }
  * { margin: 0; padding: 0; box-sizing: border-box; }
  html, body {
    width: 799px; height: 1200px; overflow: hidden;
    background: var(--backdrop);
    font-family: "Open Sans", Arial, sans-serif;
  }
  .canvas { position: relative; width: 799px; height: 1200px; }
  .card {
    position: absolute; left: 80px; width: 640px; height: 366px;
    border-radius: 3px; overflow: hidden;
    box-shadow: 0 12px 30px rgba(0,0,0,.45);
  }
  .card--front { top: 120px; background: var(--card); }
  .card--back { top: 700px; background: var(--card-back); }

  .front-brand {
    position: absolute; inset: 0;
    display: flex; align-items: center; justify-content: center; gap: 18px;
  }
  .front-brand__square { width: 44px; height: 44px; background: var(--front-mark); }
  .front-brand__name {
    font-weight: 800; font-size: 52px; letter-spacing: 1px; color: var(--front-mark);
  }

  .back-decor {
    position: absolute; right: 40px; top: 120px; width: 190px; height: 190px;
    border: 26px solid var(--faint);
  }
  .back-brand {
    position: absolute; left: 34px; top: 30px;
    display: flex; align-items: center; gap: 12px;
  }
  .back-brand__square { width: 28px; height: 28px; background: var(--ink); }
  .back-brand__name { font-weight: 800; font-size: 28px; color: var(--accent); letter-spacing: .5px; }

  .contact { position: absolute; left: 34px; top: 92px; color: var(--ink); }
  .contact__name { font-weight: 700; font-size: 21px; color: var(--accent); line-height: 1.2; }
  .contact__title { font-size: 13px; margin-top: 2px; }
  .contact__company { font-weight: 700; font-size: 16px; color: var(--accent); margin-top: 10px; }
  .contact__list { list-style: none; margin-top: 6px; font-size: 13.5px; line-height: 19px; }
  .contact__list li { display: flex; align-items: center; gap: 9px; }
  .contact__list svg { width: 12px; height: 12px; fill: var(--muted); flex: none; }
  .contact__label { color: var(--accent); }
  .contact__plain { padding-left: 0; }

  .accent-rule {
    position: absolute; left: 0; right: 0; bottom: 14px; height: 6px; background: var(--accent);
  }
</style>
</head>
<body>
<main class="canvas">
  <section class="card card--front" aria-label="Card front">
    <div class="front-brand">
      <span class="front-brand__square"></span>
      <span class="front-brand__name">ORIN VANTAGE</span>
    </div>
  </section>

  <section class="card card--back" aria-label="Card back">
    <div class="back-decor"></div>
    <div class="back-brand">
      <span class="back-brand__square"></span>
      <span class="back-brand__name">ORIN VANTAGE</span>
    </div>
    <div class="contact">
      <p class="contact__name">Clara Jo Tsang</p>
      <p class="contact__title">Vice President, &nbsp;APAC M&amp;A Operations</p>
      <p class="contact__company">Orin Vantage Asia Pacific Limited</p>
      <ul class="contact__list">
        <li><svg viewBox="0 0 12 12"><rect x="3" y="0" width="6" height="12" rx="1.2"/></svg>+852 6038 1742</li>
        <li><svg viewBox="0 0 12 12"><path d="M2 1h3l1 3-1.5 1a7 7 0 0 0 2.5 2.5L8 6l3 1v3a1 1 0 0 1-1 1A9 9 0 0 1 1 2a1 1 0 0 1 1-1z"/></svg>+852 2836 4100</li>
        <li><svg viewBox="0 0 12 12"><rect x="0" y="4" width="12" height="7" rx="1"/><rect x="3" y="0" width="6" height="5"/></svg>+852 2836 4177, &nbsp;<span class="contact__label">VOIP:</span>&nbsp;4158</li>
        <li class="contact__plain">cjtsang@orinvantage.com</li>
        <li class="contact__plain">Unit 1407, K18, 18 Tai Lok Shan Road, Hong Kong</li>
      </ul>
    </div>
    <div class="accent-rule"></div>
  </section>
</main>
</body>
</html>
```